Social Media Templates for Fieldhouse Raffle Fund

We need a set of Square (1080 x 1080) social media posts.

My company works with sports clubs, helping them to raise money with a lottery.

I need a set of social media image that I can use to appeal to new Fieldhouse Raffle Fund to encourage them to start a lottery with us.

This landing page has worked very well for us https://fieldhouserafflefund.com/fieldhouse-raffle-fund/

THING THAT APPEAL TO CLUBS

No Setup Fees/Start for Free - (We don’t charge any registration fees, or setup fees so you can start raising money from the first draw.)

Start Straight Away - (A club can start raising money straight away.)

Sustainable Income - (The average player plays for 7 years)

Subscription Lottery - (once a player joins, they play until the choose to leave. A club doesn't have to sell tickets every draw to the same people)

All Administration Taken Care Of - (We do all the hard work, so they can focus on running their club.)

Unlimited Income - (There is no limit on the amount of money a club can raise: the more players, the more funds for the club.)

Fundraising reach - (Reach new fans)

50% of the sales is guaranteed profit

£25,000 jackpot - (a person could win £25,000 every week)

Price - (It costs just £1 per week to enter)

Help Your Club - (100% of the profit goes to the club who a player chooses to support)

You can see all the clubs we work with on www.fieldhouserafflefund.com

The images will also be used on Chatterwall. You can see some examples here https://www.chatterwall.com/FieldhouseRaffleFund/ (you may need a proxy to view this page as it is only viewable in the UK, so I have attached some screenshots)

You can find the Fieldhouse Raffle Fund Logo here https://www.logovault.com/winwellgroup/

Target Market(s)

People who are involved with amateur sports in United Kingdom

Industry/Entity Type

Gambling

Font styles to use
Sans Serif

Requirements
Must have
• My project must look great on social social media and encourage people to get in touch about starting a lottery with us.

Adobe Suite files must be provided

```html
<!DOCTYPE html>
<html lang="en">
<head>
<meta charset="utf-8">
<title>Fieldhouse Raffle Fund — Social Post Set</title>
<link rel="stylesheet" href="https://fonts.googleapis.com/css2?family=Teko:wght@500;600&family=Montserrat:wght@400;500;600&display=swap">
<style>
  :root {
    --ink: #07090c;
    --navy: #0b1630;
    --deep: #0d1f3c;
    --blue: #2778cc;
    --sky: #3a9be3;
    --white: #ffffff;
    --sheet: #ffffff;
  }
  html, body { margin: 0; padding: 0; overflow: hidden; }
  body { width: 1200px; height: 914px; background: var(--sheet); position: relative; }
  .post { position: absolute; width: 246px; height: 246px; box-shadow: 0 2px 6px rgba(0,0,0,.28); background: var(--ink); overflow: hidden; }
  .post svg { display: block; width: 100%; height: 100%; }
  .hd { font-family: 'Teko', sans-serif; font-weight: 600; }
  .bd { font-family: 'Montserrat', sans-serif; font-weight: 500; }
  .mark { font-family: 'Teko', sans-serif; font-weight: 500; fill: var(--white); }
</style>
</head>
<body>

<!-- Row one -->
<div class="post post--free" style="left:59px;top:63px">
  <svg viewBox="0 0 450 450">
    <rect width="450" height="450" fill="var(--ink)"/>
    <rect x="110" y="0" width="260" height="250" fill="#5a7d3a" role="img" aria-label="Photo of a smiling boy holding a football"/>
    <polygon points="0,300 450,230 450,450 0,450" fill="var(--blue)"/>
    <polygon points="0,424 450,360 450,450 0,450" fill="var(--white)"/>
    <g class="mark"><text x="30" y="60" font-size="22">FIELDHOUSE</text><text x="30" y="82" font-size="22">RAFFLE FUND</text></g>
    <g transform="rotate(-8 225 330)">
      <rect x="75" y="222" width="300" height="56" fill="var(--white)"/>
      <text class="hd" x="225" y="270" font-size="60" fill="var(--ink)" text-anchor="middle" textLength="270" lengthAdjust="spacingAndGlyphs">START FOR</text>
      <text class="hd" x="225" y="378" font-size="140" fill="var(--white)" text-anchor="middle" textLength="290" lengthAdjust="spacingAndGlyphs">FREE</text>
    </g>
    <g transform="rotate(-8 225 414)" class="bd" font-size="10" fill="var(--ink)" text-anchor="middle">
      <text x="225" y="407">We don’t charge any registration fees, or setup fees</text>
      <text x="225" y="422">so you can start raising money from the first draw.</text>
    </g>
  </svg>
</div>

<div class="post post--straight" style="left:340px;top:63px">
  <svg viewBox="0 0 450 450">
    <rect width="450" height="450" fill="var(--ink)"/>
    <polygon points="0,210 450,170 450,450 0,450" fill="var(--blue)"/>
    <polygon points="0,225 450,195 450,450 0,450" fill="#3cb4d8" role="img" aria-label="Photo of a swimmer doing breaststroke in a pool"/>
    <text class="hd" x="30" y="75" font-size="66" fill="var(--white)">START</text>
    <text class="hd" x="30" y="128" font-size="66" fill="var(--sky)">STRAIGHT</text>
    <text class="hd" x="30" y="181" font-size="66" fill="var(--white)">AWAY</text>
    <g class="mark"><text x="350" y="50" font-size="18">FIELDHOUSE</text><text x="350" y="70" font-size="18">RAFFLE FUND</text></g>
    <g class="bd" font-size="14" fill="var(--white)" text-anchor="end">
      <text x="430" y="125">A club can start raising</text>
      <text x="430" y="145">money straight away.</text>
    </g>
  </svg>
</div>

<div class="post post--sustainable" style="left:620px;top:63px">
  <svg viewBox="0 0 450 450">
    <defs><linearGradient id="g3" x1="0" y1="0" x2="0" y2="1"><stop offset="0" stop-color="#0c1b2c"/><stop offset="1" stop-color="#060a10"/></linearGradient></defs>
    <rect width="450" height="450" fill="url(#g3)"/>
    <rect x="0" y="330" width="450" height="120" fill="#1f4a2c" role="img" aria-label="Photo of a floodlit football match at night"/>
    <g class="mark" text-anchor="middle"><text x="225" y="48" font-size="18">FIELDHOUSE</text><text x="225" y="68" font-size="18">RAFFLE FUND</text></g>
    <g transform="rotate(-8 225 200)" class="hd" fill="#e8edf2" text-anchor="middle">
      <text x="225" y="200" font-size="96" textLength="350" lengthAdjust="spacingAndGlyphs">SUSTAINABLE</text>
      <text x="225" y="280" font-size="96">INCOME</text>
    </g>
    <polygon points="0,320 450,250 450,292 0,362" fill="var(--blue)"/>
    <text class="bd" x="225" y="318" font-size="17" fill="var(--white)" text-anchor="middle" transform="rotate(-8 225 310)">THE AVERAGE PLAYER PLAYS FOR 7 YEARS</text>
    <rect x="170" y="405" width="112" height="28" rx="14" fill="none" stroke="var(--sky)" stroke-width="2"/>
    <text class="bd" x="226" y="425" font-size="15" fill="var(--white)" text-anchor="middle">JOIN NOW</text>
  </svg>
</div>

<div class="post post--subscription" style="left:901px;top:63px">
  <svg viewBox="0 0 450 450">
    <rect width="450" height="450" fill="#6f8f6a" role="img" aria-label="Photo of a young man in a blue shirt at a sports ground"/>
    <polygon points="30,385 450,345 450,450 0,450" fill="var(--ink)"/>
    <polygon points="200,450 450,420 450,450" fill="var(--blue)"/>
    <polygon points="170,250 440,205 440,330 170,370" fill="var(--blue)"/>
    <g transform="rotate(-8 300 290)" class="hd" fill="var(--white)" text-anchor="middle">
      <text x="305" y="275" font-size="54" textLength="230" lengthAdjust="spacingAndGlyphs">SUBSCRIPTION</text>
      <text x="305" y="345" font-size="84" textLength="200" lengthAdjust="spacingAndGlyphs">LOTTERY</text>
    </g>
    <g transform="rotate(-8 300 400)" class="bd" font-size="11" fill="var(--white)" text-anchor="end">
      <text x="430" y="380">once a player joins, they play until the choose to</text>
      <text x="430" y="396">leave. A club doesn’t have to sell tickets every</text>
      <text x="430" y="412">draw to the same people</text>
    </g>
    <g class="mark"><text x="30" y="408" font-size="16">FIELDHOUSE</text><text x="30" y="426" font-size="16">RAFFLE FUND</text></g>
  </svg>
</div>

<!-- Row two -->
<div class="post post--admin" style="left:63px;top:342px">
  <svg viewBox="0 0 450 450">
    <rect width="450" height="450" fill="var(--navy)"/>
    <rect width="450" height="300" fill="#6c8a55" role="img" aria-label="Photo of a youth sports team with coaches on a grass field"/>
    <polygon points="0,300 450,250 450,450 0,450" fill="var(--navy)"/>
    <polygon points="50,240 410,200 410,330 50,370" fill="var(--blue)"/>
    <g transform="rotate(-7 230 290)" class="hd" fill="var(--white)" text-anchor="middle">
      <text x="230" y="285" font-size="58" textLength="320" lengthAdjust="spacingAndGlyphs">ALL ADMINISTRATION</text>
      <text x="230" y="340" font-size="58" textLength="240" lengthAdjust="spacingAndGlyphs">TAKEN CARE OF</text>
    </g>
    <g class="bd" font-size="15" fill="var(--white)">
      <text x="26" y="408">We do all the hard work, so they can</text>
      <text x="26" y="428">focus on running their club.</text>
    </g>
    <g class="mark"><text x="360" y="408" font-size="15">FIELDHOUSE</text><text x="360" y="425" font-size="15">RAFFLE FUND</text></g>
  </svg>
</div>

<div class="post post--unlimited" style="left:342px;top:342px">
  <svg viewBox="0 0 450 450">
    <rect width="450" height="450" fill="#8fa97a" role="img" aria-label="Photo of a girl kicking a football during a match"/>
    <polygon points="0,325 225,325 265,450 0,450" fill="var(--ink)"/>
    <polygon points="200,370 450,370 450,450 230,450" fill="var(--blue)"/>
    <text class="hd" x="28" y="388" font-size="58" fill="var(--white)" textLength="165" lengthAdjust="spacingAndGlyphs">UNLIMITED</text>
    <text class="hd" x="28" y="440" font-size="72" fill="var(--white)" textLength="165" lengthAdjust="spacingAndGlyphs">INCOME</text>
    <g class="bd" font-size="10.5" fill="var(--white)" text-anchor="end">
      <text x="430" y="398">There is no limit on the amount of</text>
      <text x="430" y="413">money a club can raise: the more</text>
      <text x="430" y="428">players, the more funds for the club.</text>
    </g>
    <g class="mark"><text x="350" y="50" font-size="18">FIELDHOUSE</text><text x="350" y="70" font-size="18">RAFFLE FUND</text></g>
  </svg>
</div>

<div class="post post--reach" style="left:622px;top:342px">
  <svg viewBox="0 0 450 450">
    <rect width="450" height="450" fill="#7e8f86" role="img" aria-label="Photo of a young footballer in a training bib"/>
    <polygon points="0,300 420,250 450,300 450,450 0,450" fill="var(--ink)"/>
    <polygon points="0,350 40,360 0,450" fill="var(--blue)"/>
    <polygon points="420,250 450,230 450,300" fill="var(--blue)"/>
    <g transform="rotate(-8 225 330)" class="hd" text-anchor="middle" fill="var(--sky)">
      <text x="230" y="325" font-size="76" textLength="340" lengthAdjust="spacingAndGlyphs">FUNDRAISING</text>
      <text x="200" y="392" font-size="76">REACH</text>
    </g>
    <text class="bd" x="235" y="432" font-size="20" fill="var(--white)" text-anchor="middle" transform="rotate(-8 235 425)">REACH NEW FANS</text>
    <g class="mark"><text x="350" y="50" font-size="18">FIELDHOUSE</text><text x="350" y="70" font-size="18">RAFFLE FUND</text></g>
  </svg>
</div>

<div class="post post--profit" style="left:901px;top:342px">
  <svg viewBox="0 0 450 450">
    <rect width="450" height="450" fill="var(--ink)"/>
    <polygon points="0,260 450,215 450,450 0,450" fill="var(--blue)"/>
    <polygon points="75,70 370,50 380,395 85,420" fill="none" stroke="var(--white)" stroke-width="5"/>
    <g transform="rotate(-5 225 240)" class="hd" fill="var(--white)" text-anchor="middle">
      <text x="225" y="185" font-size="100" textLength="250" lengthAdjust="spacingAndGlyphs">50% OF</text>
      <text x="225" y="255" font-size="82" textLength="270" lengthAdjust="spacingAndGlyphs">THE SALES IS</text>
      <text x="225" y="315" font-size="78" textLength="270" lengthAdjust="spacingAndGlyphs">GUARANTEED</text>
      <text x="225" y="405" font-size="120" textLength="270" lengthAdjust="spacingAndGlyphs">PROFIT</text>
    </g>
    <g class="mark" text-anchor="middle"><text x="225" y="48" font-size="18">FIELDHOUSE</text><text x="225" y="68" font-size="18">RAFFLE FUND</text></g>
  </svg>
</div>

<!-- Row three -->
<div class="post post--jackpot" style="left:201px;top:624px">
  <svg viewBox="0 0 450 450">
    <rect width="450" height="450" fill="#7f8a6c" role="img" aria-label="Photo of an older couple holding a prize cheque and champagne"/>
    <polygon points="0,255 225,320 450,255 450,450 0,450" fill="var(--white)"/>
    <polygon points="0,270 225,330 450,270 450,450 0,450" fill="var(--blue)"/>
    <text class="hd" x="225" y="398" font-size="78" fill="var(--white)" text-anchor="middle" textLength="390" lengthAdjust="spacingAndGlyphs">£25,000 JACKPOT</text>
    <text class="bd" x="225" y="432" font-size="16" fill="var(--white)" text-anchor="middle">A PERSON COULD WIN £25,000 EVERY WEEK</text>
    <g class="mark"><text x="365" y="42" font-size="17">FIELDHOUSE</text><text x="365" y="60" font-size="17">RAFFLE FUND</text></g>
  </svg>
</div>

<div class="post post--price" style="left:479px;top:624px">
  <svg viewBox="0 0 450 450">
    <rect width="450" height="450" fill="#6aa7a0" role="img" aria-label="Photo of a volleyball on a bench in a sports hall"/>
    <polygon points="0,350 450,300 450,450 0,450" fill="var(--ink)"/>
    <polygon points="0,400 450,360 450,450 0,450" fill="var(--blue)"/>
    <polygon points="0,405 250,450 0,450" fill="var(--navy)"/>
    <polygon points="20,190 280,230 275,360 15,320" fill="var(--blue)"/>
    <text class="hd" x="35" y="335" font-size="150" fill="var(--white)" textLength="230" lengthAdjust="spacingAndGlyphs" transform="rotate(5 145 290)">PRICE</text>
    <g transform="rotate(8 150 375)" class="bd" font-size="20" fill="var(--white)" text-anchor="middle">
      <text x="145" y="365">It costs just £1 per</text>
      <text x="145" y="392">week to enter</text>
    </g>
    <g class="mark"><text x="360" y="400" font-size="17">FIELDHOUSE</text><text x="360" y="418" font-size="17">RAFFLE FUND</text></g>
  </svg>
</div>

<div class="post post--help" style="left:757px;top:633px">
  <svg viewBox="0 0 450 450">
    <rect width="450" height="450" fill="var(--ink)"/>
    <polygon points="300,0 450,0 450,450 240,450 190,330" fill="#7fa6bd" role="img" aria-label="Photo of a boy windsurfing on open water"/>
    <polygon points="290,0 305,0 195,330 245,450 232,450 180,330" fill="var(--blue)"/>
    <polygon points="0,120 215,120 180,330 0,330" fill="var(--blue)"/>
    <g class="hd" fill="var(--white)">
      <text x="28" y="190" font-size="74">HELP</text>
      <text x="28" y="253" font-size="74">YOUR</text>
      <text x="28" y="316" font-size="74">CLUB</text>
    </g>
    <g class="bd" font-size="15" fill="var(--white)">
      <text x="30" y="365">100% of the profit</text>
      <text x="30" y="384">goes to the club</text>
      <text x="30" y="403">who a player</text>
      <text x="30" y="422">chooses to support</text>
    </g>
    <g class="mark"><text x="36" y="55" font-size="20">FIELDHOUSE</text><text x="36" y="77" font-size="20">RAFFLE FUND</text></g>
  </svg>
</div>

</body>
</html>
```